Veltrane Group Business Card Design

The CEO is looking for a new trendy look for his business card.
You can stay with current branding or come up with something new/creative. It can be 3D, including Medical Office buildings. You can use our logo in a variety of colors. Please include name, title, company name, company website, email address, cell number

Target Market(s)

Real Estate Development and Construction

Industry/Entity Type

Health care real estate

Contact Information for Business Card

Rohesh Kamdar, CEO M-604.781.2249 E-roheshkamdar@veltrane.com Address:4180 Lindqvist Ave, Tampa, FL 33482 www.veltrane.com

Font styles to use
Other font styles liked:
• Be creative

Requirements
Must have
• Creative, trendy look
Nice to have
• Please go to our website to get a feel- www. veltrane.com
Should not have
• small fonts

```html
<!DOCTYPE html>
<html lang="en">
<head>
<meta charset="utf-8">
<title>Veltrane Group Business Card</title>
<link href="https://fonts.googleapis.com/css2?family=Montserrat:wght@300;400;700;800&display=swap" rel="stylesheet">
<style>
  :root {
    --stage: #484848;
    --card: #171717;
    --ink: #ffffff;
    --ink-soft: #e6e6e6;
  }
  * { margin: 0; padding: 0; box-sizing: border-box; }
  html, body { width: 1200px; height: 801px; overflow: hidden; }
  body {
    background: var(--stage);
    font-family: "Montserrat", sans-serif;
    display: flex;
    align-items: center;
    justify-content: center;
    gap: 40px;
  }
  .card {
    width: 540px;
    height: 309px;
    background: var(--card);
    border-radius: 18px;
    color: var(--ink);
    position: relative;
    overflow: hidden;
  }
  /* Contact side */
  .card--contact { display: flex; align-items: center; }
  .contact__brand {
    width: 46%;
    display: flex;
    justify-content: center;
    align-items: center;
    height: 100%;
  }
  .brand-name {
    font-weight: 800;
    color: var(--ink);
    text-align: center;
    line-height: 0.95;
    letter-spacing: -0.01em;
  }
  .contact__brand .brand-name { font-size: 34px; }
  .contact__divider {
    width: 1.5px;
    height: 62%;
    background: var(--ink);
  }
  .contact__details {
    padding-left: 26px;
    display: flex;
    flex-direction: column;
  }
  .person-name {
    font-weight: 700;
    font-size: 19px;
    letter-spacing: 0.02em;
    text-transform: uppercase;
  }
  .person-title {
    font-weight: 300;
    font-size: 13px;
    margin-top: 2px;
    color: var(--ink-soft);
  }
  .address {
    font-style: normal;
    font-weight: 300;
    font-size: 13px;
    line-height: 1.4;
    margin-top: 12px;
    color: var(--ink-soft);
  }
  .contact-list { list-style: none; margin-top: 10px; }
  .contact-list li {
    display: flex;
    align-items: center;
    gap: 7px;
    font-weight: 300;
    font-size: 13px;
    line-height: 1.55;
    color: var(--ink-soft);
  }
  .contact-list svg { width: 11px; height: 11px; flex: none; }
  /* Brand side */
  .card--brand { display: flex; align-items: center; justify-content: center; }
  .card--brand .brand-name { font-size: 62px; }
</style>
</head>
<body>
  <section class="card card--contact" aria-label="Business card, contact side">
    <div class="contact__brand">
      <p class="brand-name">Veltrane<br>Group</p>
    </div>
    <div class="contact__divider"></div>
    <div class="contact__details">
      <h1 class="person-name">Rohesh Kamdar</h1>
      <p class="person-title">CEO</p>
      <address class="address">4180 Lindqvist Ave,<br>Tampa, FL 33482</address>
      <ul class="contact-list">
        <li>
          <svg viewBox="0 0 12 12" aria-hidden="true"><rect x="3" y="0.8" width="6" height="10.4" rx="1" fill="none" stroke="#fff" stroke-width="1.1"/><circle cx="6" cy="9.4" r="0.6" fill="#fff"/></svg>
          604.781.2249
        </li>
        <li>
          <svg viewBox="0 0 12 12" aria-hidden="true"><rect x="0.5" y="2.2" width="11" height="7.6" fill="#fff"/><path d="M0.8 2.6 6 6.8 11.2 2.6" fill="none" stroke="#171717" stroke-width="1"/></svg>
          roheshkamdar@veltrane.com
        </li>
        <li>
          <svg viewBox="0 0 12 12" aria-hidden="true"><circle cx="6" cy="6" r="5.2" fill="#fff"/><path d="M0.8 6h10.4M6 0.8c-2.4 2.8-2.4 7.6 0 10.4M6 0.8c2.4 2.8 2.4 7.6 0 10.4" fill="none" stroke="#171717" stroke-width="0.8"/></svg>
          www.veltrane.com
        </li>
      </ul>
    </div>
  </section>

  <section class="card card--brand" aria-label="Business card, brand side">
    <p class="brand-name">Veltrane<br>Group</p>
  </section>
</body>
</html>
```